Talvique Hotels Business Card and Logo

We need a business card design for a hotel group. I saw a hotel card you designed and really liked it. We have multiple properties with different brands. Were hoping that the card would be unique and find a way to list out all our properties. Our web address is www.talviquehotels.com. I have attached some photos of card designs I like.

Industry/Entity Type

Hotel

Contact Information for Business Card

Scott CurranReneson HotelsChief Operating Officer56 Madera DriveCorte Madera, CA 94925Office 415-891-5013Cell 707-5550143

```html
<!DOCTYPE html>
<html lang="en">
<head>
<meta charset="utf-8">
<title>Talvique Hotels Business Card</title>
<link rel="stylesheet" href="https://fonts.googleapis.com/css2?family=Oswald:wght@300;400&family=Tinos:wght@400;700&display=swap">
<style>
  :root {
    --backdrop: #8f8f8f;
    --slate: #476579;
    --slate-light: #5d7d92;
    --paper: #ffffff;
    --paper-shade: #eef1f3;
    --ink-light: #f4f7f9;
  }
  * { margin: 0; padding: 0; box-sizing: border-box; }
  html, body {
    width: 1200px; height: 941px; overflow: hidden;
    background: var(--backdrop);
  }
  .sheet {
    width: 1200px; height: 941px;
    display: flex; flex-direction: column; align-items: center; justify-content: center;
    gap: 60px;
  }
  .card {
    position: relative;
    width: 620px; height: 354px;
    border-radius: 14px;
    overflow: hidden;
  }
  .card--back {
    background: radial-gradient(ellipse at 62% 68%, var(--slate-light) 0%, var(--slate) 60%);
  }
  .brand-block { position: absolute; }
  .brand-row { display: flex; align-items: center; gap: 14px; }
  .brand-mark { flex: none; border-radius: 50%; }
  .brand-name {
    font-family: 'Oswald', sans-serif;
    font-weight: 300;
    letter-spacing: 0.5px;
    line-height: 1;
    white-space: nowrap;
  }
  .tagline {
    font-family: 'Oswald', sans-serif; font-weight: 400;
    font-size: 7px; letter-spacing: 0.4px; text-transform: uppercase;
    margin-top: 4px; white-space: nowrap;
  }
  .card--back .brand-block { left: 150px; top: 92px; }
  .card--back .brand-mark { width: 60px; height: 60px; background: var(--ink-light); opacity: 0.85; }
  .card--back .brand-name { font-size: 58px; color: var(--ink-light); }
  .card--back .tagline { color: var(--ink-light); margin-left: 74px; }
  .web {
    position: absolute; left: 40px; bottom: 48px;
    font-family: 'Tinos', serif; font-size: 20px; letter-spacing: 3px;
    color: var(--ink-light);
  }
  .card--front {
    background: radial-gradient(ellipse at 40% 75%, var(--slate-light) 0%, var(--slate) 65%);
  }
  .front-band {
    position: absolute; left: 0; top: 0; width: 100%; height: 150px;
    background: linear-gradient(180deg, var(--paper) 60%, var(--paper-shade) 100%);
  }
  .card--front .brand-block { left: 150px; top: 46px; }
  .card--front .brand-mark { width: 52px; height: 52px; background: var(--slate); }
  .card--front .brand-name { font-size: 52px; color: var(--slate); }
  .card--front .tagline { color: var(--slate); margin-left: 66px; }
  .contact {
    position: absolute; left: 0; top: 170px; width: 100%;
    text-align: center;
    font-family: 'Tinos', serif; color: var(--ink-light);
  }
  .contact__name { font-weight: 700; font-size: 26px; letter-spacing: 0.5px; }
  .contact__title { font-size: 19px; margin-bottom: 6px; }
  .contact__line { font-size: 18px; line-height: 1.3; }
</style>
</head>
<body>
  <main class="sheet">
    <section class="card card--back">
      <div class="brand-block">
        <div class="brand-row">
          <span class="brand-mark"></span><span class="brand-name">Talvique Hotels</span>
        </div>
        <p class="tagline">Restful stays in the finest coastal, valley and hillside towns of the West</p>
      </div>
      <p class="web">www.talviquehotels.com</p>
    </section>

    <section class="card card--front">
      <div class="front-band"></div>
      <div class="brand-block">
        <div class="brand-row">
          <span class="brand-mark"></span><span class="brand-name">Talvique Hotels</span>
        </div>
        <p class="tagline">Restful stays in the finest coastal, valley and hillside towns of the West</p>
      </div>
      <div class="contact">
        <p class="contact__name">Brent Holloway</p>
        <p class="contact__title">Hotels Chief Operating Officer</p>
        <p class="contact__line">83 Pellwick Lane, Ashford Vale, CA 94768</p>
        <p class="contact__line">Office : 415-555-0186</p>
        <p class="contact__line">Cell : 707-5550143</p>
      </div>
    </section>
  </main>
</body>
</html>
```